TA BRAMLEY BUSINESS CARD DESIGN PROJECT

We need to utilize our logo that was expertly created on PixelHarbor and now need to match this with a business card design.

```html
<!DOCTYPE html>
<html lang="en">
<head>
<meta charset="UTF-8">
<title>TA Bramley Business Card</title>
<link rel="stylesheet" href="https://fonts.googleapis.com/css2?family=Montserrat:wght@400;500;700;800&display=swap">
<style>
  :root {
    --stage: #262626;
    --card: #161616;
    --brand-blue: #1258b0;
    --ink-light: #f2f2f2;
    --emboss: #2a2a2a;
  }
  * { box-sizing: border-box; margin: 0; padding: 0; }
  html, body { width: 1200px; height: 900px; overflow: hidden; }
  body {
    background: var(--stage);
    font-family: "Montserrat", sans-serif;
    display: flex;
    align-items: center;
    justify-content: center;
    gap: 40px;
  }
  .card {
    position: relative;
    width: 540px;
    height: 310px;
    border-radius: 18px;
    background: var(--card);
    overflow: hidden;
  }
  .card-back { border: 3px solid var(--brand-blue); }

  .wave { position: absolute; inset: 0; width: 100%; height: 100%; }

  .brand-name {
    position: absolute;
    left: 40px;
    top: 112px;
    width: 210px;
    font-weight: 800;
    font-size: 30px;
    line-height: 1.1;
    letter-spacing: 3px;
    color: var(--brand-blue);
  }
  .divider {
    position: absolute;
    left: 270px;
    top: 50px;
    width: 1px;
    height: 150px;
    background: var(--brand-blue);
  }
  .contact {
    position: absolute;
    left: 290px;
    top: 46px;
    color: var(--ink-light);
  }
  .contact-name {
    font-weight: 700;
    font-size: 17px;
    color: var(--brand-blue);
    letter-spacing: 0.5px;
  }
  .contact-role { font-size: 12px; margin-top: 2px; }
  .contact-list { list-style: none; margin-top: 12px; font-size: 11.5px; }
  .contact-list li { display: flex; align-items: center; gap: 7px; line-height: 17px; }
  .contact-list svg { width: 11px; height: 11px; fill: var(--ink-light); }
  .contact-address { margin-top: 12px; font-size: 11.5px; line-height: 17px; }

  .back-name {
    position: absolute;
    inset: 0;
    display: flex;
    align-items: center;
    justify-content: center;
    font-weight: 800;
    font-size: 52px;
    letter-spacing: 6px;
    color: var(--emboss);
  }
</style>
</head>
<body>
  <section class="card card-front">
    <svg class="wave" viewBox="0 0 540 310" preserveAspectRatio="none" aria-hidden="true">
      <path d="M20 310 C90 275 220 262 330 262 C420 262 500 250 540 225 L540 310 Z" fill="var(--brand-blue)"/>
      <path d="M6 302 C80 262 215 250 330 250 C420 250 495 238 540 212" fill="none" stroke="var(--brand-blue)" stroke-width="4"/>
    </svg>
    <div class="brand-name">TA<br>BRAMLEY</div>
    <div class="divider"></div>
    <div class="contact">
      <p class="contact-name">OWEN HARTLEY</p>
      <p class="contact-role">Managing Director</p>
      <ul class="contact-list">
        <li><svg viewBox="0 0 12 12"><path d="M2 1h3l1 3-2 1a6 6 0 0 0 3 3l1-2 3 1v3c-6 0-9-3-9-9z"/></svg>123 456 789</li>
        <li><svg viewBox="0 0 12 12"><path d="M3 0h6v3H3zM1 4h10v6H1zM3 8h6v4H3z"/></svg>123 456 789</li>
        <li><svg viewBox="0 0 12 12"><path d="M0 2h12v1L6 7 0 3zM0 4l6 4 6-4v6H0z"/></svg>info@tabramley.com</li>
        <li><svg viewBox="0 0 12 12"><circle cx="6" cy="6" r="6"/></svg>www.tabramley.com</li>
      </ul>
      <p class="contact-address">Your address, City<br>State, Zip 1234</p>
    </div>
  </section>

  <section class="card card-back">
    <div class="back-name">TA BRAMLEY</div>
  </section>
</body>
</html>
```